Talvonne Capital LLC

Need Professional Business cards for New Investment Fund

Target Market(s)

High Quality investors

Industry/Entity Type

Financial

Contact Information for Business Card

Phone Number +1 555 284 6190
Name Lukas Varenko
Title Fund Manager
email lv@FundCorvel.com
Website www.FundCorvel.com

Colors

Designer to choose colors to be used in the design.

Requirements
Must have
• Must have our Logo and all of the above. Must be made so lettering and loge can be raised

```html
<!DOCTYPE html>
<html lang="en">
<head>
<meta charset="utf-8">
<title>Talvonne Capital LLC — Business Card</title>
<link rel="stylesheet" href="https://fonts.googleapis.com/css2?family=Roboto:wght@400;500;700&display=swap">
<style>
  :root {
    --bg: #d6d7d8;
    --card-white: #ffffff;
    --brand-green: #14e600;
    --brand-green-deep: #0fcf00;
    --ink-gray: #555a55;
    --rule-gray: #b9bcb9;
    --on-green: #ffffff;
  }
  * { margin: 0; padding: 0; box-sizing: border-box; }
  html, body {
    width: 1200px; height: 801px; overflow: hidden;
    background: var(--bg);
    font-family: "Roboto", Arial, sans-serif;
  }
  .stage {
    width: 1200px; height: 801px;
    display: flex; align-items: center; justify-content: center; gap: 40px;
  }
  .card {
    width: 540px; height: 309px; position: relative;
    box-shadow: 0 10px 28px rgba(0,0,0,.18);
  }
  .card-front { background: var(--card-white); }
  .card-back { background: var(--brand-green); overflow: hidden; }

  .front-brand {
    position: absolute; left: 40px; top: 142px;
    display: flex; align-items: center; gap: 10px;
    color: var(--ink-gray); font-weight: 500; font-size: 18px; letter-spacing: .4px;
    white-space: nowrap;
  }
  .brand-dot { width: 14px; height: 14px; border-radius: 50%; background: var(--brand-green); flex: none; }
  .front-divider {
    position: absolute; left: 232px; top: 96px; width: 1px; height: 118px;
    background: var(--rule-gray);
  }
  .front-details { position: absolute; left: 258px; top: 98px; }
  .person-name { color: var(--brand-green); font-weight: 700; font-size: 21px; line-height: 1.1; }
  .person-title { color: var(--ink-gray); font-size: 13px; margin-top: 4px; }
  .contact-list { list-style: none; margin-top: 14px; }
  .contact-item {
    display: flex; align-items: center; gap: 8px;
    color: var(--ink-gray); font-size: 13px; line-height: 20px;
  }
  .contact-icon { width: 10px; height: 10px; flex: none; }

  .back-field { position: absolute; inset: 0; background: linear-gradient(160deg, #1cf00a 0%, var(--brand-green) 50%, var(--brand-green-deep) 100%); }
  .back-brand {
    position: absolute; right: 30px; bottom: 30px;
    color: var(--on-green); font-weight: 500; font-size: 17px; letter-spacing: .4px;
    white-space: nowrap;
  }
</style>
</head>
<body>
<main class="stage">
  <section class="card card-front" aria-label="Card front">
    <div class="front-brand"><span class="brand-dot"></span><span>Talvonne Capital</span></div>
    <div class="front-divider"></div>
    <div class="front-details">
      <h1 class="person-name">Lukas Varenko</h1>
      <p class="person-title">Fund Manager</p>
      <ul class="contact-list">
        <li class="contact-item">
          <svg class="contact-icon" viewBox="0 0 10 10"><path d="M2 0.5 L3.8 2.6 L2.8 3.8 Q4 6.2 6.2 7.2 L7.4 6.2 L9.5 8 L8.2 9.5 Q3 9 0.5 1.8 Z" fill="var(--brand-green)"/></svg>
          <span>+1 555 284 6190</span>
        </li>
        <li class="contact-item">
          <svg class="contact-icon" viewBox="0 0 10 10"><rect x="0.5" y="2" width="9" height="6.5" fill="var(--brand-green)"/><path d="M0.8 2.3 L5 5.6 L9.2 2.3" fill="none" stroke="#fff" stroke-width="0.9"/></svg>
          <span>lv@FundCorvel.com</span>
        </li>
        <li class="contact-item">
          <svg class="contact-icon" viewBox="0 0 10 10"><circle cx="5" cy="5" r="4.5" fill="var(--brand-green)"/><path d="M0.5 5 H9.5 M5 0.5 Q2.5 5 5 9.5 M5 0.5 Q7.5 5 5 9.5" fill="none" stroke="#fff" stroke-width="0.7"/></svg>
          <span>www.FundCorvel.com</span>
        </li>
      </ul>
    </div>
  </section>

  <section class="card card-back" aria-label="Card back">
    <div class="back-field" role="img" aria-label="Repeating raised brand-mark pattern in tonal green"></div>
    <div class="back-brand">Talvonne Capital</div>
  </section>
</main>
</body>
</html>
```